Podiatry clinic requires a modern revamp and editing of existing website.

I would like a fresh new look and updated information for my current business website. An easy to navigate site with prominent address and phone number for call to action. We are a podiatry clinic that focuses on general and sports podiatry.
I would like 4 pages; including Home page, About Us, Services & Contact.
www.brambleridgepodiatry.net

Target Market(s)

Active working professionals.

Industry/Entity Type

Medical

Coding

Coded - Design and coding required

Number of Pages Required

4 page

Font styles to use
Sans Serif

Colors
6b449b

Requirements
Must have
• A modern look with logo and active images; clean and uncluttered. Visible phone number and address for call to action.
• 4 pages - Home, About Us, Services, Contact.
• Home page - update address & service logos.
• About Us - update of personal information.
• Services - Revamp of existing page.
• Contact page to include Google map, email & phone number.
Nice to have
• Ability to add content easily; eg. a blog or adding video onto Home page.
• Link to Facebook page.

```html
<!DOCTYPE html>
<html lang="en">
<head>
<meta charset="utf-8">
<title>Bramble Ridge Podiatry</title>
<link href="https://fonts.googleapis.com/css2?family=Open+Sans:wght@400;600&display=swap" rel="stylesheet">
<style>
:root{
  --orange:#f58a4a;
  --orange-deep:#ec6a1f;
  --purple:#6b449b;
  --lilac:#9a84c4;
  --navy:#3b2a86;
  --text:#555;
  --dark:#222;
  --green:#7fbe3a;
  --sky:#d6eef6;
  --foot-grey:#f2f2f2;
}
*{margin:0;padding:0;box-sizing:border-box}
html,body{width:849px;height:1200px;overflow:hidden;background:#fff}
body{font-family:"Open Sans",Arial,sans-serif;color:var(--text);position:relative}
.abs{position:absolute}
.site-header{left:0;top:0;width:849px;height:92px;background:linear-gradient(90deg,#f7945a,#f6884a 60%,#f48d55)}
.brand{left:94px;top:0;width:116px;height:92px;background:var(--lilac);display:flex;align-items:center;justify-content:center;text-align:center;color:#fff;font-weight:600;font-size:13px;line-height:15px;padding:0 8px}
.topline{right:95px;top:24px;font-size:8.5px;color:#fff;display:flex;gap:8px;align-items:center}
.topline svg{width:7px;height:7px;margin-right:3px;vertical-align:-1px}
.nav{right:95px;top:58px;display:flex;gap:24px;font-size:9.5px;color:#fff;text-transform:uppercase}
.nav .active{color:var(--dark)}
.hero{left:0;top:92px;width:849px;height:343px;background:linear-gradient(100deg,#e9e9ea 0%,#f3efec 30%,#eadbd1 50%,#3d4150 75%,#d9d9db 100%)}
.arrow{top:252px;width:17px;height:23px;background:rgba(120,120,120,.5);display:flex;align-items:center;justify-content:center}
.arrow svg{width:7px;height:11px}
.welcome{left:0;top:465px;width:849px;text-align:center}
.welcome h1{font-size:18.5px;font-weight:600;color:var(--navy)}
.welcome p{width:660px;margin:6px auto 0;font-size:7.4px;line-height:14px;color:#555}
.cta{left:344px;top:548px;width:163px;height:28px;background:var(--orange-deep);color:#fff;font-size:10.5px;display:flex;align-items:center;justify-content:center;border-radius:2px}
.enquiry{left:0;top:589px;width:849px;text-align:center;font-size:10px;color:var(--orange-deep)}
.director{left:0;top:637px;width:849px;height:232px;background:linear-gradient(180deg,#cbe9f4,#e7f4f9 60%,#d4edf5)}
.portrait{left:95px;top:620px;width:235px;height:249px;background:linear-gradient(180deg,#d9e6ec,#f2f5f7 55%,#e4ecf2);border-radius:90px 90px 0 0}
.role{left:268px;top:669px;font-size:11px;color:var(--dark)}
.name{left:268px;top:684px;font-size:20px;font-weight:600;color:var(--navy)}
.creds{left:270px;top:709px;font-size:9.5px;color:var(--dark)}
.bio{left:434px;top:669px;width:322px;font-size:7.4px;line-height:13.6px;color:#222}
.bio p+p{margin-top:13.6px}
.more{left:434px;top:802px;width:58px;height:22px;background:#fff;font-size:7px;color:#444;display:flex;align-items:center;justify-content:center}
.tile{top:869px;height:170px}
.tile-general{left:0;width:424px;background:linear-gradient(120deg,#4a4a4a,#7a6a66 40%,#c9a890 60%,#555 100%)}
.tile-special{left:424px;width:425px;background:linear-gradient(90deg,#c9ccd1,#e6e7ea 55%,#f1e3d9 80%,#eef0f3)}
.label{top:1005px;height:34px;color:#fff;font-size:14px;font-weight:600;display:flex;align-items:center;justify-content:center;letter-spacing:.3px}
.label-general{left:251px;width:173px;background:var(--green)}
.label-special{left:424px;width:195px;background:var(--orange)}
.badge{top:1068px;height:38px;border-radius:4px}
.footer{left:0;top:1132px;width:849px;height:68px;background:var(--foot-grey)}
.foot-links{left:94px;top:1151px;font-size:7.5px;color:#333}
.copy{left:94px;top:1169px;font-size:7.5px;color:#333}
.social{top:1156px;width:18px;height:18px;border-radius:50%}
</style>
</head>
<body>
<header class="site-header abs"></header>
<div class="brand abs">Bramble Ridge Podiatry</div>
<div class="topline abs">
  <span><svg viewBox="0 0 10 10"><path d="M5 0a3.5 3.5 0 0 0-3.5 3.5C1.5 6 5 10 5 10s3.5-4 3.5-6.5A3.5 3.5 0 0 0 5 0zm0 5a1.5 1.5 0 1 1 0-3 1.5 1.5 0 0 1 0 3z" fill="#fff"/></svg>Suite 12 / 88 Larkspur Lane Brookvale 3121</span><span>|</span>
  <span><svg viewBox="0 0 10 10"><path d="M2 0l2 2.5-1 1.5a6 6 0 0 0 3 3l1.5-1L10 8l-1.5 2C4 10 0 6 0 1.5z" fill="#fff"/></svg>Phone 03 9555 0142</span><span>|</span>
  <span><svg viewBox="0 0 10 10"><rect x="0" y="1.5" width="10" height="7" fill="#fff"/><path d="M0 1.5l5 4 5-4" stroke="#f58a4a" fill="none"/></svg>info@brambleridgepodiatry.net</span>
</div>
<nav class="nav abs"><span class="active">Home</span><span>About Us</span><span>Podiatry Services</span><span>Contact</span></nav>

<div class="hero abs" role="img" aria-label="Photo of hands massaging the sole of a bare foot"></div>
<div class="arrow abs" style="left:0"><svg viewBox="0 0 7 11"><path d="M6 1L1 5.5 6 10" stroke="#fff" fill="none"/></svg></div>
<div class="arrow abs" style="right:0"><svg viewBox="0 0 7 11"><path d="M1 1l5 4.5L1 10" stroke="#fff" fill="none"/></svg></div>

<section class="welcome abs">
  <h1>Welcome to Bramble Ridge Podiatry</h1>
  <p>Bramble Ridge Podiatry is a Podiatry clinic in the heart of the Brookvale centre. We are located between Fern &amp; Hollis Streets in the Larkspur Business Centre / Wren Hotel Complex. Our podiatrists are fully qualified health professionals who are able to diagnose, treat, manage or help to prevent all medical conditions that affect the feet and lower limb. We provide General Podiatry Treatment and some Specialised Services in relation to various foot conditions, including Sports Injuries, Orthotic Therapy and Nail Surgery.</p>
</section>
<div class="cta abs">Click Here For Appointments</div>
<div class="enquiry abs">Enquiries please call us on 03 9555 0142 orEmail : info@brambleridgepodiatry.net</div>

<section class="director abs"></section>
<div class="portrait abs" role="img" aria-label="Portrait of the clinic director in a white coat with a stethoscope"></div>
<div class="role abs">Director / Chief Podiatrist</div>
<div class="name abs">Helen Marsh</div>
<div class="creds abs">B.Pod. M.AMS. M.RASP</div>
<div class="bio abs">
  <p>Helen graduated from Eastmoor University in Brookvale with a Bachelor of Podiatry degree in 1994. She currently holds full registration with the Podiatry Registration Board and the National Health Practitioner Registry (NHPR). She is a full member of Active Medicine Society (AMS) and the Regional Academy of Sports Podiatry (RASP).</p>
  <p>Helen has been working in various professional capacities since 1995, predominately in the private sector. She established Bramble Ridge Podiatry in the Brookvale centre in 2009.</p>
</div>
<div class="more abs">Read more</div>

<div class="tile tile-general abs" role="img" aria-label="Photo of cared-for feet with polished toenails resting on stones beside flowers"></div>
<div class="tile tile-special abs" role="img" aria-label="Photo of hands treating the sole of a foot"></div>
<div class="label label-general abs">General Treatments</div>
<div class="label label-special abs">Specialised Treatments</div>

<div class="badge abs" style="left:164px;width:94px;background:#e8e6f2" role="img" aria-label="Partner badge"></div>
<div class="badge abs" style="left:290px;width:88px;background:#e3ecf6" role="img" aria-label="Partner badge"></div>
<div class="badge abs" style="left:411px;width:115px;background:#ececec" role="img" aria-label="Partner badge"></div>
<div class="badge abs" style="left:566px;width:120px;background:#e2f1e5" role="img" aria-label="Partner badge"></div>

<footer class="footer abs"></footer>
<div class="foot-links abs">Home &nbsp; | &nbsp; About Us &nbsp; | &nbsp; Podiatry Services &nbsp; | &nbsp; Contact</div>
<div class="copy abs">Copyright &copy; 2016 &nbsp;Bramble Ridge Podiatry. &nbsp;All rights reserved.</div>
<div class="social abs" style="left:690px;background:#3b5a9a" aria-label="Social link"></div>
<div class="social abs" style="left:713px;background:#2aa3e0" aria-label="Social link"></div>
<div class="social abs" style="left:736px;background:#1a78b5" aria-label="Social link"></div>
</body>
</html>
```